Brintel Works - Fast, Efficient and Gas Mainteance for Domestic, Commercial and Industrial clients

We are in the process of purchasing a new business and would like to get a new logo and business card.
Business is a gas maintenance business that also does new gas installations.
Has been established since 1988.
Services include:
Install all types of gas appliances & equipment inc. hot water units
Maintain / repair / replace all types of gas appliances & equipment

Target Market(s)

Domestic, Commercial and Industrial clients

Industry/Entity Type

Business

Contact Information for Business Card

admin@brintelworks.com.au
07 3918 4726
Brintel Works PTY LTD

Logo Text

Gas Fitting & Plumbing Maintenance Specialists

Font styles to use
Sans Serif

Requirements
Must have
• Logo
• Business name, contact number, email address, web address
• Domestic | Commercial | Industrial Est Since 1988
Nice to have
• Possibly a black card with a flame logo to one side
Should not have
• Spelling errors

```html
<!DOCTYPE html>
<html lang="en">
<head>
<meta charset="utf-8">
<title>Brintel Works – Business Card</title>
<link href="https://fonts.googleapis.com/css2?family=Montserrat:wght@500;600;800&display=swap" rel="stylesheet">
<style>
  :root {
    --page-bg: #2b2622;
    --card-black: #050505;
    --text-white: #ffffff;
    --accent-orange: #f47b20;
    --flame-red: #ec3a24;
    --flame-amber: #f9a21b;
    --body-text: #f2f2f2;
  }
  * { margin: 0; padding: 0; box-sizing: border-box; }
  html, body { width: 1200px; height: 1000px; overflow: hidden; }
  body {
    background: var(--page-bg);
    font-family: "Montserrat", Arial, sans-serif;
    position: relative;
  }
  .card {
    position: absolute;
    left: 266px;
    width: 664px;
    height: 397px;
    background: var(--card-black);
    border-radius: 22px;
    overflow: hidden;
  }
  .card--front { top: 73px; }
  .card--back { top: 533px; }

  .brand-dot {
    position: absolute;
    border-radius: 50%;
    background: linear-gradient(180deg, var(--flame-amber), var(--flame-red));
  }
  .brand-name {
    position: absolute;
    color: var(--text-white);
    font-weight: 800;
    line-height: 1;
    letter-spacing: 0.02em;
  }
  .brand-name span { display: block; }
  .brand-name .legal { letter-spacing: 0.14em; }

  .card--front .brand-dot { left: 42px; top: 62px; width: 86px; height: 86px; }
  .card--front .brand-name { left: 157px; top: 88px; font-size: 29px; }
  .card--front .brand-name .legal { font-size: 14px; margin-top: 6px; }

  .contact-name {
    position: absolute;
    left: 157px; top: 188px;
    color: var(--accent-orange);
    font-weight: 600;
    font-size: 17px;
  }
  .contact-list {
    position: absolute;
    left: 157px; top: 220px;
    list-style: none;
    color: var(--body-text);
    font-size: 14.5px;
    font-weight: 500;
  }
  .contact-list li { display: flex; align-items: center; gap: 8px; height: 22px; }
  .contact-list svg { width: 13px; height: 13px; fill: var(--accent-orange); }
  .services {
    position: absolute;
    left: 157px; top: 277px;
    width: 300px;
    color: var(--body-text);
    font-size: 14.5px;
    font-weight: 500;
    line-height: 20.5px;
  }
  .accent-bar {
    position: absolute;
    left: 0; right: 0; bottom: 0;
    height: 20px;
    background: linear-gradient(90deg, var(--flame-red), var(--flame-amber) 45%, var(--flame-red));
  }

  .card--back .brand-dot { left: 130px; top: 105px; width: 135px; height: 135px; }
  .card--back .brand-name { left: 292px; top: 155px; font-size: 35px; }
  .card--back .brand-name .legal { font-size: 18px; margin-top: 8px; }
</style>
</head>
<body>
  <section class="card card--front" aria-label="Business card front">
    <div class="brand-dot" aria-hidden="true"></div>
    <div class="brand-name"><span>BRINTEL WORKS</span><span class="legal">PTY LTD</span></div>
    <p class="contact-name">Mara Ellison</p>
    <ul class="contact-list">
      <li>
        <svg viewBox="0 0 24 24" aria-hidden="true"><path d="M6.6 10.8a15.1 15.1 0 0 0 6.6 6.6l2.2-2.2c.3-.3.7-.4 1-.2 1.1.4 2.3.6 3.6.6.6 0 1 .4 1 1V20c0 .6-.4 1-1 1A17 17 0 0 1 3 4c0-.6.4-1 1-1h3.5c.6 0 1 .4 1 1 0 1.3.2 2.5.6 3.6.1.3 0 .7-.2 1z"/></svg>
        07 3918 4726
      </li>
      <li>
        <svg viewBox="0 0 24 24" aria-hidden="true"><path d="M2 5h20v14H2z M2 5l10 8 10-8" /></svg>
        admin@brintelworks.com.au
      </li>
    </ul>
    <p class="services">Install all types of gas appliances &amp; equipment inc. hot water units Maintain / repair / replace all types of gas appliances &amp; equipment</p>
    <div class="accent-bar"></div>
  </section>

  <section class="card card--back" aria-label="Business card back">
    <div class="brand-dot" aria-hidden="true"></div>
    <div class="brand-name"><span>BRINTEL WORKS</span><span class="legal">PTY LTD</span></div>
  </section>
</body>
</html>
```